Delegate visit agenda

We need a creative, yet simple and official design for an agenda to be handed out for delegates visiting our organization. The design needs to be creative, informative and visual when possible. Flat design is desired but other options are welcomed. The agenda should be 3 pages in lengths only. Page 1 should have the company logo with an event title (with the ability to add country flag) and the dates of the event. Pages 2 should include photos of receiving delegate (e.g. VIPs) and any other relevant people. Page 3 should include agenda entries with the following information: title of entry, date and time, location, relevant pictures (e.g. a hotel or flight). The generic style of an infographic.
Updates
Project Deadline Extended
Reason: Not enough submissions received.
No optimal design (i.e. creative and attractive) received.

Brief has been updated with samples.

Target Market(s)
Very high profile people (e.g. presidents, ministers, GM,...etc.)
Industry/Entity Type
Hotel
Colors
Designer to choose colors to be used in the design.
Look and feel
Each slider illustrates characteristics of the customer's brand and the style your logo design should communicate.

```html
<!DOCTYPE html>
<html lang="en">
<head>
<meta charset="utf-8">
<title>Programme</title>
<link rel="stylesheet" href="https://fonts.googleapis.com/css2?family=Arvo:wght@400;700&family=Roboto+Slab:wght@300;400&family=Arimo:wght@400&display=swap">
<style>
  :root {
    --gold: #c08a2e;
    --red: #e2231a;
    --ink: #231f20;
    --paper: #ffffff;
  }
  html, body {
    margin: 0;
    padding: 0;
    width: 1200px;
    height: 849px;
    overflow: hidden;
    background: var(--paper);
  }
  .page {
    position: relative;
    width: 1200px;
    height: 849px;
    overflow: hidden;
    background: var(--paper);
    color: var(--ink);
    font-family: "Roboto Slab", "Rockwell", serif;
  }
  .page-title {
    position: absolute;
    top: 36px;
    right: 42px;
    margin: 0;
    font-family: "Arvo", "Rockwell", serif;
    font-size: 28px;
    font-weight: 700;
    line-height: 34px;
    letter-spacing: 0.3px;
  }
  .timeline-art {
    position: absolute;
    inset: 0;
  }
  .entry {
    position: absolute;
    width: 199px;
    margin: 0;
  }
  .entry-title {
    margin: 0;
    text-align: center;
    font-family: "Arvo", "Rockwell", serif;
    font-size: 15.5px;
    font-weight: 700;
    line-height: 20px;
  }
  .entry-subtitle {
    margin: 1px 0 5px;
    text-align: center;
    font-family: "Roboto Slab", "Rockwell", serif;
    font-size: 11.5px;
    font-weight: 400;
    line-height: 15px;
  }
  .entry-text {
    margin: 0;
    text-align: justify;
    text-align-last: left;
    font-family: "Roboto Slab", "Rockwell", serif;
    font-size: 10.6px;
    font-weight: 300;
    line-height: 15.6px;
  }
  .entry--upper { top: 199px; }
  .entry--lower { top: 461px; }
  .legend {
    position: absolute;
    left: 104px;
    top: 796px;
    margin: 0;
    padding: 0;
    list-style: none;
    font-family: "Arimo", sans-serif;
    font-size: 11px;
  }
  .legend-item {
    position: absolute;
    top: 0;
    display: flex;
    align-items: center;
    gap: 5px;
    white-space: nowrap;
    height: 32px;
  }
  .legend-icon {
    width: 30px;
    height: 30px;
    color: var(--ink);
  }
</style>
</head>
<body>
<main class="page">
  <h1 class="page-title">PROGRAMME</h1>

  <svg class="timeline-art" width="1200" height="849" viewBox="0 0 1200 849" aria-hidden="true">
    <defs>
      <symbol id="icon-pin" viewBox="0 0 24 24">
        <path fill="currentColor" d="M12 1.5a7.5 7.5 0 0 0-7.5 7.5c0 5.5 7.5 13.5 7.5 13.5s7.5-8 7.5-13.5A7.5 7.5 0 0 0 12 1.5z"/>
        <circle cx="12" cy="9" r="2.8" fill="#fff"/>
      </symbol>
      <symbol id="icon-diamond" viewBox="0 0 24 24">
        <polygon fill="currentColor" points="2,8.5 6.5,3 17.5,3 22,8.5 12,21.5"/>
        <path fill="none" stroke="#fff" stroke-width="0.9" d="M2.5 8.5h19M6.5 3l2.5 5.5L12 3l3 5.5L17.5 3M9 8.5l3 12.5 3-12.5"/>
      </symbol>
      <symbol id="icon-lotus" viewBox="0 0 24 24">
        <path fill="currentColor" d="M12 4c2.3 2.2 3 5 3 7.5S13.8 16 12 17c-1.8-1-3-3-3-5.5S9.7 6.2 12 4z"/>
        <path fill="currentColor" d="M4 9c3 .3 5.5 2.3 6.5 4.8.6 1.5.8 2.7.8 3.6C8.3 17 5.2 15 4.4 12.2 4.1 11 4 10 4 9zM20 9c-3 .3-5.5 2.3-6.5 4.8-.6 1.5-.8 2.7-.8 3.6 3-.4 6.1-2.4 6.9-5.2.3-1.2.4-2.2.4-3.2z"/>
        <path fill="currentColor" d="M3 18.2h18c-1.5 1.2-4 1.8-9 1.8s-7.5-.6-9-1.8z"/>
      </symbol>
      <symbol id="icon-banquet" viewBox="0 0 24 24">
        <circle cx="12" cy="12" r="11.5" fill="currentColor"/>
        <g transform="translate(4.8 4.2) scale(0.6)" color="#fff"><use href="#icon-lotus"/></g>
      </symbol>
      <symbol id="icon-clock" viewBox="0 0 24 24">
        <path fill="currentColor" d="M3.2 6.8a3.4 3.4 0 0 1 4.7-4.7zM20.8 6.8a3.4 3.4 0 0 0-4.7-4.7z"/>
        <circle cx="12" cy="13" r="8" fill="none" stroke="currentColor" stroke-width="2.2"/>
        <path fill="none" stroke="currentColor" stroke-width="1.8" stroke-linecap="round" d="M12 8.5V13l3 2M6.5 21.5l1.5-2M17.5 21.5l-1.5-2"/>
      </symbol>
      <symbol id="icon-compass" viewBox="0 0 24 24">
        <circle cx="12" cy="12" r="10" fill="none" stroke="currentColor" stroke-width="1.8"/>
        <polygon fill="currentColor" points="16.5,6.5 13.2,13.2 11,11"/>
        <polygon fill="none" stroke="currentColor" stroke-width="1" points="7.5,17.5 10.8,10.8 13,13"/>
        <path stroke="currentColor" stroke-width="1.2" d="M12 2.5v2M12 19.5v2M2.5 12h2M19.5 12h2"/>
      </symbol>
      <symbol id="icon-chat" viewBox="0 0 24 24">
        <path fill="none" stroke="currentColor" stroke-width="1.7" stroke-linejoin="round" d="M2 3h13v8.5H8L5 14v-2.5H2z"/>
        <path fill="#fff" stroke="currentColor" stroke-width="1.7" stroke-linejoin="round" d="M8 9h14v9h-3v2.8L16 18H8z"/>
      </symbol>
      <symbol id="icon-gears" viewBox="0 0 24 24">
        <g fill="none" stroke="currentColor">
          <circle cx="8" cy="8" r="4.3" stroke-width="2.6"/>
          <circle cx="8" cy="8" r="6" stroke-width="2.4" stroke-dasharray="2.1 2.6"/>
          <circle cx="16" cy="16" r="3.8" stroke-width="2.4"/>
          <circle cx="16" cy="16" r="5.4" stroke-width="2.2" stroke-dasharray="1.9 2.3"/>
        </g>
      </symbol>
      <symbol id="icon-plane" viewBox="0 0 24 24">
        <path fill="currentColor" d="M22.5 3.2c-.8-.6-2.4-.2-3.8.7L15 6.6 6 4.5 4.2 5.7l7.2 3.8-3.8 2.9-3.3-.6L3 12.6l3.3 2 1.3 3.4 1.3-.7-.2-3.4 4.3-2 1.1 8 2-1.1.7-9.2 3.5-2.8c1.3-1.1 2.5-2.5 1.9-3.6z"/>
      </symbol>
      <g id="node">
        <circle r="6.5" fill="var(--gold)"/>
        <circle r="4.6" fill="#fff"/>
        <circle r="3" fill="var(--red)"/>
      </g>
      <g id="badge-down">
        <path fill="var(--gold)" d="M-6 28 L0 38 L6 28 Z"/>
        <circle r="30" fill="var(--gold)"/>
      </g>
      <g id="badge-up">
        <path fill="var(--gold)" d="M-6 -28 L0 -38 L6 -28 Z"/>
        <circle r="30" fill="var(--gold)"/>
      </g>
    </defs>

    <line x1="56" y1="403.5" x2="1146" y2="403.5" stroke="var(--gold)" stroke-width="5.4" stroke-linecap="round" stroke-dasharray="0 11.47"/>

    <g stroke="var(--gold)" stroke-width="2.6" fill="none">
      <path d="M83 193.5h140M42 350.5h222M153 350.5V606"/>
      <path d="M377 193.5h140M336 350.5h222M447 350.5V606"/>
      <path d="M670 193.5h140M629 350.5h222M740 350.5V606"/>
      <path d="M976 193.5h140M935 350.5h222M1046 350.5V606"/>
      <path d="M300 203V456.5M189 456.5h222M230 612.5h140"/>
      <path d="M594 203V456.5M483 456.5h222M524 612.5h140"/>
      <path d="M887 203V456.5M776 456.5h222M817 612.5h140"/>
    </g>

    <use href="#node" x="153" y="403.5"/>
    <use href="#node" x="300" y="403.5"/>
    <use href="#node" x="447" y="403.5"/>
    <use href="#node" x="594" y="403.5"/>
    <use href="#node" x="740" y="403.5"/>
    <use href="#node" x="887" y="403.5"/>
    <use href="#node" x="1046" y="403.5"/>

    <g transform="translate(300 166)"><use href="#badge-down"/><use href="#icon-clock" x="-17" y="-17" width="34" height="34" color="var(--red)"/></g>
    <g transform="translate(594 166)"><use href="#badge-down"/><use href="#icon-chat" x="-18" y="-18" width="36" height="36" color="var(--red)"/></g>
    <g transform="translate(887 166)"><use href="#badge-down"/><use href="#icon-gears" x="-18" y="-18" width="36" height="36" color="var(--red)"/></g>

    <g transform="translate(153 641)"><use href="#badge-up"/><use href="#icon-diamond" x="-19" y="-19" width="38" height="38" color="var(--red)"/></g>
    <g transform="translate(447 641)"><use href="#badge-up"/><use href="#icon-compass" x="-17" y="-17" width="34" height="34" color="var(--red)"/></g>
    <g transform="translate(740 641)"><use href="#badge-up"/><circle r="19" fill="var(--red)"/><use href="#icon-lotus" x="-12" y="-13" width="24" height="24" color="var(--gold)"/></g>
    <g transform="translate(1046 641)"><use href="#badge-up"/><use href="#icon-plane" x="-21" y="-21" width="42" height="42" color="var(--red)"/></g>
  </svg>

  <article class="entry entry--upper" style="left:54px">
    <h2 class="entry-title">Lorem ipsum</h2>
    <p class="entry-subtitle">LOREM IPSUM</p>
    <p class="entry-text">Lorem ipsum dolor sit amet, error regione voluptua mea ei, ei ullum civibus efficiantur pri. Ei exerci reprimique has. Duo te dicant complectitur, pri ei</p>
  </article>
  <article class="entry entry--upper" style="left:348px">
    <h2 class="entry-title">Lorem ipsum</h2>
    <p class="entry-subtitle">LOREM IPSUM</p>
    <p class="entry-text">Lorem ipsum dolor sit amet, error regione voluptua mea ei, ei ullum civibus efficiantur pri. Ei exerci reprimique has. Duo te dicant complectitur, pri ei</p>
  </article>
  <article class="entry entry--upper" style="left:641px">
    <h2 class="entry-title">Lorem ipsum</h2>
    <p class="entry-subtitle">LOREM IPSUM</p>
    <p class="entry-text">Lorem ipsum dolor sit amet, error regione voluptua mea ei, ei ullum civibus efficiantur pri. Ei exerci reprimique has. Duo te dicant complectitur, pri ei</p>
  </article>
  <article class="entry entry--upper" style="left:947px">
    <h2 class="entry-title">Lorem ipsum</h2>
    <p class="entry-subtitle">LOREM IPSUM</p>
    <p class="entry-text">Lorem ipsum dolor sit amet, error regione voluptua mea ei, ei ullum civibus efficiantur pri. Ei exerci reprimique has. Duo te dicant complectitur, pri ei</p>
  </article>

  <article class="entry entry--lower" style="left:201px">
    <h2 class="entry-title">Lorem ipsum</h2>
    <p class="entry-subtitle">LOREM IPSUM</p>
    <p class="entry-text">Lorem ipsum dolor sit amet, error regione voluptua mea ei, ei ullum civibus efficiantur pri. Ei exerci reprimique has. Duo te dicant complectitur, pri ei</p>
  </article>
  <article class="entry entry--lower" style="left:494px">
    <h2 class="entry-title">Lorem ipsum</h2>
    <p class="entry-subtitle">LOREM IPSUM</p>
    <p class="entry-text">Lorem ipsum dolor sit amet, error regione voluptua mea ei, ei ullum civibus efficiantur pri. Ei exerci reprimique has. Duo te dicant complectitur, pri ei</p>
  </article>
  <article class="entry entry--lower" style="left:788px">
    <h2 class="entry-title">Lorem ipsum</h2>
    <p class="entry-subtitle">LOREM IPSUM</p>
    <p class="entry-text">Lorem ipsum dolor sit amet, error regione voluptua mea ei, ei ullum civibus efficiantur pri. Ei exerci reprimique has. Duo te dicant complectitur, pri ei</p>
  </article>

  <ul class="legend">
    <li class="legend-item" style="left:0"><svg class="legend-icon" viewBox="0 0 24 24"><use href="#icon-pin"/></svg>Hotel</li>
    <li class="legend-item" style="left:98px"><svg class="legend-icon" viewBox="0 0 24 24"><use href="#icon-diamond"/></svg>Delegate Event</li>
    <li class="legend-item" style="left:244px"><svg class="legend-icon" viewBox="0 0 24 24"><use href="#icon-banquet"/></svg>Banquet</li>
    <li class="legend-item" style="left:364px"><svg class="legend-icon" viewBox="0 0 24 24"><use href="#icon-clock"/></svg>Breakfast Meeting</li>
    <li class="legend-item" style="left:523px"><svg class="legend-icon" viewBox="0 0 24 24"><use href="#icon-compass"/></svg>Tour</li>
    <li class="legend-item" style="left:618px"><svg class="legend-icon" viewBox="0 0 24 24"><use href="#icon-chat"/></svg>Presentations</li>
    <li class="legend-item" style="left:764px"><svg class="legend-icon" viewBox="0 0 24 24"><use href="#icon-gears"/></svg>Working Meeting</li>
    <li class="legend-item" style="left:918px"><svg class="legend-icon" viewBox="0 0 24 24" style="width:36px;height:36px"><use href="#icon-plane"/></svg>Departure</li>
  </ul>
</main>
</body>
</html>
```